Roofing Company Modern look

I want a modern and sophisticated look for our roofing business.

Our address is :

5217 Mallow Creek Ln
Orlando, Fl 32825

(407)-583-2196

www.HarborlineRoofsFl.com

I also want to make sure on the back there is a spot to put
Project Manager Name :

Number:

Because the cards will be used by all sales people

Project Manager Name :

Also there are accreditation we have logos are uploaded here as well that I would like maybe on the back of card as well

I also want to highlight our special attributions or trades:

Residential & Commercial
Fully Insured
License # CCC7482913
Insurance Claims
Serving Central Florida Since 1992
Free Estimates

Contact Information for Business Card

Our address is :

5217 Mallow Creek Ln
Orlando, Fl 32825

(407)-583-2196

Project Manager Name :

Residential & Commercial
Fully Insured
License # CCC7482913
Insurance Claims
Free Estimates

Font styles to use
Serif
Sans Serif

Colors
3176b5

Requirements
Must have
• Must have royal blue like my logo grey and black are the colors I like

```html
<!DOCTYPE html>
<html lang="en">
<head>
<meta charset="utf-8">
<title>Harborline Roofing &amp; Gutters – Business Card</title>
<link rel="stylesheet" href="https://fonts.googleapis.com/css2?family=Exo+2:wght@400;600&family=Oswald:wght@500&family=Montserrat:wght@500;600&display=swap">
<style>
  :root {
    --royal: #1f6db5;
    --royal-deep: #0d5aa6;
    --royal-light: #3a8fd0;
    --slate: #4d535c;
    --ink: #4a4a4a;
    --rule: #2f5a46;
    --paper: #ffffff;
    --backdrop: #e9eaec;
  }
  * { box-sizing: border-box; margin: 0; padding: 0; }
  html, body { width: 1200px; height: 1200px; overflow: hidden; }
  body { background: var(--backdrop); position: relative; font-family: "Exo 2", sans-serif; }

  .card {
    position: absolute; left: 150px; width: 900px; height: 514px;
    background: var(--paper); border-radius: 26px; overflow: hidden;
  }
  .card--front { top: 56px; }
  .card--back { top: 630px; }

  .front-shapes { position: absolute; inset: 0; width: 100%; height: 100%; }

  .brand { position: absolute; left: 400px; top: 170px; width: 380px; text-align: center; color: var(--royal); font-family: "Exo 2", sans-serif; font-weight: 600; }
  .brand__mark { width: 64px; height: 64px; border-radius: 50%; background: var(--royal); margin: 0 auto 18px; }
  .brand__name { font-size: 50px; letter-spacing: 3px; line-height: 1; }
  .brand__sub { font-size: 17px; letter-spacing: 3px; margin-top: 10px; }

  .contact { position: absolute; left: 47px; top: 322px; color: var(--paper); }
  .contact__phone { font-family: "Oswald", sans-serif; font-weight: 500; font-size: 38px; line-height: 1; letter-spacing: 0.5px; }
  .contact__address { font-size: 22px; line-height: 29px; margin-top: 14px; letter-spacing: 0.5px; }
  .contact__web { font-size: 23px; margin-top: 8px; }

  .field { position: absolute; left: 62px; right: 63px; display: flex; align-items: baseline; color: var(--royal-deep); font-family: "Montserrat", sans-serif; font-weight: 600; font-size: 21px; }
  .field--manager { top: 60px; }
  .field--phone { top: 134px; }
  .field__line { flex: 1; margin-left: 8px; border-bottom: 2px dotted var(--royal-deep); transform: translateY(-3px); }

  .rule { position: absolute; left: 62px; right: 63px; height: 2px; background: var(--rule); }
  .rule--top { top: 211px; }
  .rule--bottom { top: 337px; }

  .attributes { position: absolute; top: 234px; list-style: none; font-family: "Montserrat", sans-serif; font-weight: 600; font-size: 19px; color: var(--ink); }
  .attributes--left { left: 62px; }
  .attributes--right { left: 473px; }
  .attributes li { display: flex; align-items: center; height: 28px; }
  .tick { width: 14px; height: 14px; margin-right: 11px; flex: none; }

  .badge { position: absolute; }
  .badge--listing { left: 84px; top: 380px; width: 90px; height: 90px; border-radius: 50%; background: #5a5f66; }
  .badge--rating { left: 252px; top: 373px; width: 62px; height: 96px; border-radius: 4px; background: #1d4f86; }
  .badge--manufacturer { left: 392px; top: 393px; width: 226px; height: 66px; background: #c8242b; border: 3px solid #1d2a55; }
  .badge--applicator { left: 703px; top: 381px; width: 88px; height: 88px; background: #23345e; transform: rotate(45deg) scale(0.85); }
</style>
</head>
<body>

<section class="card card--front" aria-label="Card front">
  <svg class="front-shapes" viewBox="0 0 800 457" preserveAspectRatio="none" aria-hidden="true">
    <defs>
      <linearGradient id="blueSweep" x1="0" y1="0" x2="1" y2="1">
        <stop offset="0" stop-color="#0d5aa6"/>
        <stop offset="0.55" stop-color="#2a86cc"/>
        <stop offset="1" stop-color="#0f62ad"/>
      </linearGradient>
    </defs>
    <path d="M480,0 L800,0 L800,205 C740,95 640,20 480,0 Z" fill="#4d535c"/>
    <path d="M0,0 L8,0 C120,230 360,400 800,384 L800,457 L0,457 Z" fill="url(#blueSweep)"/>
  </svg>

  <div class="brand">
    <div class="brand__mark"></div>
    <div class="brand__name">HARBORLINE</div>
    <div class="brand__sub">ROOFING &amp; GUTTERS INC.</div>
  </div>

  <div class="contact">
    <p class="contact__phone">(407)-583-2196</p>
    <p class="contact__address">5217 Mallow Creek Ln<br>Orlando, Fl 32825</p>
    <p class="contact__web">www.HarborlineRoofsFl.com</p>
  </div>
</section>

<section class="card card--back" aria-label="Card back">
  <div class="field field--manager"><span>PROJECT MANAGER NAME :</span><span class="field__line"></span></div>
  <div class="field field--phone"><span>PHONE :</span><span class="field__line"></span></div>

  <div class="rule rule--top"></div>

  <ul class="attributes attributes--left">
    <li><svg class="tick" viewBox="0 0 14 14"><circle cx="7" cy="7" r="7" fill="#1f6db5"/><path d="M3.8,7.2 L6.1,9.4 L10.3,4.8" stroke="#fff" stroke-width="1.8" fill="none"/></svg>Residential &amp; Commercial</li>
    <li><svg class="tick" viewBox="0 0 14 14"><circle cx="7" cy="7" r="7" fill="#1f6db5"/><path d="M3.8,7.2 L6.1,9.4 L10.3,4.8" stroke="#fff" stroke-width="1.8" fill="none"/></svg>Fully Insured</li>
    <li><svg class="tick" viewBox="0 0 14 14"><circle cx="7" cy="7" r="7" fill="#1f6db5"/><path d="M3.8,7.2 L6.1,9.4 L10.3,4.8" stroke="#fff" stroke-width="1.8" fill="none"/></svg>License # CCC7482913</li>
  </ul>
  <ul class="attributes attributes--right">
    <li><svg class="tick" viewBox="0 0 14 14"><circle cx="7" cy="7" r="7" fill="#1f6db5"/><path d="M3.8,7.2 L6.1,9.4 L10.3,4.8" stroke="#fff" stroke-width="1.8" fill="none"/></svg>Insurance Claims</li>
    <li><svg class="tick" viewBox="0 0 14 14"><circle cx="7" cy="7" r="7" fill="#1f6db5"/><path d="M3.8,7.2 L6.1,9.4 L10.3,4.8" stroke="#fff" stroke-width="1.8" fill="none"/></svg>Serving Central Florida Since 1992</li>
    <li><svg class="tick" viewBox="0 0 14 14"><circle cx="7" cy="7" r="7" fill="#1f6db5"/><path d="M3.8,7.2 L6.1,9.4 L10.3,4.8" stroke="#fff" stroke-width="1.8" fill="none"/></svg>Free Estimates</li>
  </ul>

  <div class="rule rule--bottom"></div>

  <div class="badge badge--listing" role="img" aria-label="Screened and approved listing badge"></div>
  <div class="badge badge--rating" role="img" aria-label="Accredited business rating badge"></div>
  <div class="badge badge--manufacturer" role="img" aria-label="Authorized roofing contractor badge"></div>
  <div class="badge badge--applicator" role="img" aria-label="Master shingle applicator badge"></div>
</section>

</body>
</html>
```